Business Card Design

I already have a company logo for my company. I have a logo for the manufacturer we represent. I want a professional business card design.

```html
<!DOCTYPE html>
<html lang="en">
<head>
<meta charset="utf-8">
<title>Beacon Alert LLC — Business Card</title>
<link rel="stylesheet" href="https://fonts.googleapis.com/css2?family=Open+Sans:wght@400;700;800&display=swap">
<style>
  :root {
    --backdrop-top: #5a5a5a;
    --backdrop-bottom: #1c1c1c;
    --card: #161616;
    --card-edge: #222222;
    --brand-red: #e3242b;
    --text-light: #ececec;
    --text-muted: #bdbdbd;
  }
  * { margin: 0; padding: 0; box-sizing: border-box; }
  html, body { width: 1200px; height: 780px; overflow: hidden; }
  body {
    background: linear-gradient(160deg, var(--backdrop-top), var(--backdrop-bottom));
    font-family: "Open Sans", Arial, sans-serif;
    display: flex;
    flex-direction: column;
    align-items: center;
    justify-content: center;
    gap: 36px;
  }
  .card {
    position: relative;
    width: 580px;
    height: 332px;
    background: var(--card);
    border: 1px solid var(--card-edge);
    border-radius: 18px;
    overflow: hidden;
    box-shadow: 0 14px 30px rgba(0,0,0,.45);
  }

  /* Information side */
  .brand-mark {
    display: flex;
    align-items: center;
    gap: 10px;
    color: var(--brand-red);
    font-weight: 800;
    letter-spacing: .04em;
    text-transform: uppercase;
  }
  .brand-mark__square { width: 14px; height: 14px; background: var(--brand-red); }
  .card--info .brand-mark { position: absolute; left: 40px; top: 40px; font-size: 22px; }

  .contact {
    position: absolute;
    left: 40px;
    top: 118px;
    color: var(--text-light);
    font-size: 15px;
    line-height: 1.55;
  }
  .contact__address { margin-bottom: 14px; }
  .contact__list { list-style: none; }
  .contact__item { display: flex; align-items: center; gap: 10px; }
  .contact__icon { width: 14px; height: 14px; fill: var(--brand-red); flex: none; }

  .holder {
    position: absolute;
    right: 58px;
    bottom: 38px;
    text-align: right;
  }
  .holder__name {
    color: var(--brand-red);
    font-weight: 700;
    font-size: 26px;
    letter-spacing: .02em;
    text-transform: uppercase;
    line-height: 1.2;
  }
  .holder__title { color: var(--text-light); font-size: 16px; }

  .edge-band {
    position: absolute;
    right: 0;
    bottom: 28px;
    width: 20px;
    height: 68px;
    background: var(--brand-red);
  }

  /* Brand side */
  .card--brand {
    display: flex;
    align-items: center;
    justify-content: center;
  }
  .card--brand .brand-mark { font-size: 40px; gap: 16px; }
  .card--brand .brand-mark__square { width: 26px; height: 26px; }
</style>
</head>
<body>

  <section class="card card--info" aria-label="Business card, contact side">
    <div class="brand-mark">
      <span class="brand-mark__square"></span>
      <span class="brand-mark__name">Beacon Alert LLC</span>
    </div>

    <div class="contact">
      <p class="contact__address">Your address, City<br>State, Zip 1234</p>
      <ul class="contact__list">
        <li class="contact__item">
          <svg class="contact__icon" viewBox="0 0 24 24" aria-hidden="true"><path d="M6.6 10.8a15 15 0 0 0 6.6 6.6l2.2-2.2c.3-.3.7-.4 1-.2 1.1.4 2.3.6 3.6.6.6 0 1 .4 1 1V20c0 .6-.4 1-1 1A17 17 0 0 1 3 4c0-.6.4-1 1-1h3.5c.6 0 1 .4 1 1 0 1.3.2 2.5.6 3.6.1.3 0 .7-.2 1z"/></svg>
          <span>123 456 789</span>
        </li>
        <li class="contact__item">
          <svg class="contact__icon" viewBox="0 0 24 24" aria-hidden="true"><path d="M3 5h18v14H3zm2 2v.5l7 4.5 7-4.5V7zm0 2.9V17h14V9.9l-7 4.5z"/></svg>
          <span>info@youremail.com</span>
        </li>
        <li class="contact__item">
          <svg class="contact__icon" viewBox="0 0 24 24" aria-hidden="true"><path d="M12 2a10 10 0 1 0 0 20 10 10 0 0 0 0-20zm6.9 9h-3a15 15 0 0 0-1.3-5.6A8 8 0 0 1 18.9 11zM12 4c.9 1.2 1.8 3.6 1.9 7h-3.8c.1-3.4 1-5.8 1.9-7zM9.4 5.4A15 15 0 0 0 8.1 11h-3a8 8 0 0 1 4.3-5.6zM5.1 13h3a15 15 0 0 0 1.3 5.6A8 8 0 0 1 5.1 13zM12 20c-.9-1.2-1.8-3.6-1.9-7h3.8c-.1 3.4-1 5.8-1.9 7zm2.6-1.4a15 15 0 0 0 1.3-5.6h3a8 8 0 0 1-4.3 5.6z"/></svg>
          <span>www.yourwebsite.com</span>
        </li>
      </ul>
    </div>

    <div class="holder">
      <p class="holder__name">Daniel Hart</p>
      <p class="holder__title">Managing Director</p>
    </div>

    <span class="edge-band" aria-hidden="true"></span>
  </section>

  <section class="card card--brand" aria-label="Business card, brand side">
    <div class="brand-mark">
      <span class="brand-mark__square"></span>
      <span class="brand-mark__name">Beacon Alert LLC</span>
    </div>
  </section>

</body>
</html>
```